Printing Company needs Website

PLEASE REVIEW ALL IMAGES, I HAVE INCLUDED A WEBSITE MOCKUP IDEA AND LOGO FILES IN THESE IMAGES.

Vel-Marks Provides printing services to multiple businesses. We Focus on 4 main markets. Signage (Signs, Banners, Wraps, Custom graphics), Printing (flyers, brochures, business cards, Postcards), Apparel (printed shirts, hoodies, sweatshirts), Promotional Products (mugs, golf balls, brava cans, pens), We try to sell ourselves on total brand imaging, our slogan is "Mark Everything." because we want to be able to provide any type of printing to our customers. Consumer targeting should be targeted towards small business, and wholesale targeting should be geared toward, merchandising, branding, marketing, design, signage, apparel, embroidery, and printing groups. WE DO OFFER DESIGN SERVICES, I have attached one orlwick guild logo design as an example.

I need a website designed both for wholesale and consumer based people. Wholesale customers would have their own login and consumers would also have their own.
I need there to be an online designer software (possibly java) built in so that the customer can order their product or upload their artwork online to see the proof for approval. There will need to be an commence setup, and I do have a quillpay account if that helps. Shipping must be auto calculated at the time of ordering. I would Like to make it to where when customer orders a product if it is outside of the dimensions requested on the site that the customer is warned of clipping or skewing.

I will be working closely aside the designer I pick to aid in the uploading and configuration of pricing structure, weight, and imagery if selected. This will be a lengthy project, and I will be willing to pay for the additional help so long as you are completely aware of the needs, Happy designing!!
Updates

I love all of the designs so far everyone! I will be reviewing PLEASE NOTE, IF I APPROVE YOUR WEB DESIGN, I WILL WANT YOU TO COMPLETE THE ENTIRE DESIGN INCLUDING A DESIGN PROOFING SETUP FOR MY CUSTOMERS INTEGRATED IN AS I HAVE STATED IN THE ORIGINAL STATEMENT. PLEASE ASK QUESTIONS IF YOU DON'T UNDERSTAND!

Target Market(s)

Small Business, School Athletics, Merchandising groups, Branding Groups, Larger Printers, Sign makers, Embroidery shops, Screen Printing Shops

Industry/Entity Type

It Company

Font styles to use
Sans Serif

Colors
000000
1b1b1b
757575
ec1f27

Requirements
Must have
• Built in design setup to each product with sizing, Ability to add pre-designed templates, .pdf print ready files after upload, Wholesale account, or Business accounts all with different pricing structures, Must be willing to aid in setup of all products and services (willing pay additional for setup costs.)
Nice to have
• SEO Optimization, targeting specific groups listed, automatic ordering to outsource vendors straight from site listing drop ship location if need be.

```html
<!DOCTYPE html>
<html lang="en">
<head>
<meta charset="utf-8">
<title>Vel-Marks — Mark Everything.</title>
<link rel="stylesheet" href="https://fonts.googleapis.com/css2?family=Roboto+Slab:wght@300;400&family=Roboto+Condensed:wght@700&family=Roboto:wght@400&display=swap">
<style>
:root{
  --black:#000000;
  --panel:#1b1b1b;
  --grey:#757575;
  --dark-grey:#4a4a4a;
  --red:#ec1f27;
  --white:#ffffff;
  --line:#3a3a3a;
}
*{margin:0;padding:0;box-sizing:border-box}
html,body{width:981px;height:1200px;overflow:hidden;background:var(--white)}
body{position:relative;font-family:"Roboto Slab",serif;color:var(--dark-grey)}
.abs{position:absolute}

/* header */
.site-header{position:absolute;left:0;top:0;width:981px;height:93px;background:var(--black)}
.nav-item{position:absolute;top:38px;font-size:11.5px;color:var(--white);letter-spacing:.2px;white-space:nowrap}
.nav-item.active{top:29px;left:80px;width:65px;height:32px;border:1px solid var(--red);border-radius:9px;color:var(--red);text-align:center;line-height:30px}
.brand{position:absolute;left:437px;top:30px;width:110px;text-align:center;color:var(--white);font-weight:400;line-height:1}
.brand-name{font-size:19px;letter-spacing:.5px}
.brand-tag{font-size:7px;margin-top:3px;text-align:right;padding-right:6px}

/* hero */
.hero{position:absolute;left:0;top:93px;width:981px;height:455px;
  background:linear-gradient(180deg,#6b9fd6 0%,#a9c8ea 16%,#f2f3f4 22%,#e6e8ea 45%,#4a5560 55%,#5d7048 66%,#a9a59e 80%,#c9c5bd 100%)}
.hero-title{position:absolute;left:0;top:370px;width:981px;text-align:center;font-family:"Roboto Condensed",sans-serif;font-weight:700;font-size:42px;color:var(--white);letter-spacing:.3px;text-shadow:0 1px 3px rgba(0,0,0,.3)}
.hero-dots{position:absolute;left:0;top:512px}

/* welcome */
.welcome-title{position:absolute;left:0;top:572px;width:981px;text-align:center;font-size:21px;font-weight:400;color:var(--dark-grey)}
.welcome-text{position:absolute;left:150px;top:608px;width:681px;text-align:center;font-size:10.5px;line-height:18px;color:var(--grey);font-weight:300}

/* services */
.service{position:absolute;top:670px;width:132px;height:190px;text-align:center}
.service svg{display:block;margin:0 auto}
.service-label{margin-top:28px;font-size:21px;color:var(--dark-grey);letter-spacing:.3px;white-space:nowrap;margin-left:-40px;margin-right:-40px}

/* footer */
.site-footer{position:absolute;left:0;top:897px;width:981px;height:253px;background:var(--panel);color:var(--white)}
.footer-heading{position:absolute;top:34px;font-size:16px;font-weight:400;white-space:nowrap}
.footer-heading::after{content:"";position:absolute;left:0;top:23px;width:24px;height:2.5px;background:var(--red)}
.link-list{position:absolute;left:82px;top:82px;width:108px;list-style:none}
.link-list li{height:28px;border-bottom:1px solid var(--line);font-size:11px;line-height:22px;padding-left:1px}
.tweet{position:absolute;left:224px;top:89px}
.tweet-text{position:absolute;left:251px;top:88px;width:170px;font-size:10.5px;line-height:16.8px}
.btn-more{position:absolute;left:251px;top:171px;width:60px;height:23px;border:1px solid var(--white);font-size:10.5px;line-height:21px;text-align:center}
.contact-list{position:absolute;left:479px;top:82px;width:157px;list-style:none}
.contact-list li{height:29px;border-bottom:1px solid var(--line);font-size:10.5px;line-height:22px}
.contact-list li.email{text-decoration:underline}
.contact-list li.address{border:none;line-height:17px;padding-top:6px;height:auto}
.news-text{position:absolute;left:681px;top:86px;width:210px;font-size:10.5px;line-height:17px}
.news-form{position:absolute;left:681px;top:134px;width:221px;height:37px;border:1px solid var(--white)}
.news-input{position:absolute;left:10px;top:0;line-height:35px;font-size:11px}
.news-send{position:absolute;right:0;top:0;width:37px;height:35px;background:var(--red)}
.social{position:absolute;left:682px;top:194px}

/* bottom bar */
.bottom-bar{position:absolute;left:0;top:1150px;width:981px;height:50px;background:var(--black);color:var(--white);font-family:"Roboto",sans-serif;font-size:11.5px}
.bottom-bar span{position:absolute;top:17px;white-space:nowrap}
</style>
</head>
<body>

<header class="site-header">
  <span class="nav-item active">HOME</span>
  <span class="nav-item" style="left:165px">ABOUT US</span>
  <span class="nav-item" style="left:251px">SIGNAGE</span>
  <span class="nav-item" style="left:330px">PRINTING</span>
  <div class="brand">
    <div class="brand-name">VEL-MARKS</div>
    <div class="brand-tag">Mark Everything.</div>
  </div>
  <span class="nav-item" style="left:582px">DESIGN</span>
  <span class="nav-item" style="left:656px">PROMOTIONAL</span>
  <span class="nav-item" style="left:767px">APPAREL</span>
  <span class="nav-item" style="left:850px">CONTACT</span>
</header>

<section class="hero" role="img" aria-label="Photo of a business entrance with a white awning, glass doors, benches and landscaped shrubs">
  <div class="hero-title" style="top:277px">MARK EVERYTHING</div>
  <svg class="hero-dots" width="981" height="12" viewBox="0 0 981 12" style="top:419px">
    <g fill="none" stroke="#fff" stroke-width="2">
      <circle cx="452" cy="6" r="4.5"/>
      <circle cx="478" cy="6" r="4.5" stroke="#333"/>
      <circle cx="503" cy="6" r="4.5"/>
      <circle cx="529" cy="6" r="4.5"/>
    </g>
  </svg>
</section>

<h1 class="welcome-title">WELCOME TO VEL MARKS</h1>
<p class="welcome-text">Praesentium voluptatum deleniti atque corrupti quos dolores et quas molestias excepturi sint occaecati cupiditate non provident, similique sunt in culpa qui officia deserunt mollitia animi, id est laborum et dolorum fuga.</p>

<div class="service" style="left:80px">
  <svg width="132" height="132" viewBox="0 0 132 132">
    <circle cx="66" cy="66" r="65" fill="none" stroke="#ddd"/>
    <circle cx="66" cy="66" r="53" fill="#4a4a4a"/>
    <path d="M48 46h36v24l-18 10-18-10z" fill="none" stroke="#fff" stroke-width="4"/>
    <path d="M55 42v8M77 42v8" stroke="#fff" stroke-width="3"/>
    <circle cx="66" cy="60" r="7" fill="none" stroke="#fff" stroke-width="2"/>
  </svg>
  <div class="service-label">SIGNAGE</div>
</div>

<div class="service" style="left:309px">
  <svg width="132" height="132" viewBox="0 0 132 132">
    <circle cx="66" cy="66" r="65" fill="none" stroke="var(--red)"/>
    <circle cx="66" cy="66" r="53" fill="var(--red)"/>
    <rect x="52" y="43" width="28" height="12" rx="2" fill="#fff"/>
    <rect x="44" y="53" width="44" height="22" rx="5" fill="#fff"/>
    <rect x="52" y="66" width="28" height="18" rx="2" fill="#fff" stroke="var(--red)" stroke-width="2"/>
    <path d="M57 72h18M57 78h18" stroke="var(--red)" stroke-width="2"/>
  </svg>
  <div class="service-label">PRINTING</div>
</div>

<div class="service" style="left:532px">
  <svg width="132" height="132" viewBox="0 0 132 132">
    <circle cx="66" cy="66" r="65" fill="none" stroke="#ddd"/>
    <circle cx="66" cy="66" r="53" fill="#4a4a4a"/>
    <path d="M44 62l40-14 10 12-38 16z" fill="#fff"/>
    <path d="M44 66c6 8 14 10 12 10M40 58h14M38 64h10M40 70h10" stroke="#fff" stroke-width="2" fill="none"/>
  </svg>
  <div class="service-label">APPAREL</div>
</div>

<div class="service" style="left:758px">
  <svg width="132" height="132" viewBox="0 0 132 132">
    <circle cx="66" cy="66" r="65" fill="none" stroke="#ddd"/>
    <circle cx="66" cy="66" r="53" fill="#4a4a4a"/>
    <rect x="42" y="50" width="46" height="32" fill="none" stroke="#fff" stroke-width="4"/>
    <path d="M66 82v6M56 90h20" stroke="#fff" stroke-width="4"/>
    <path d="M52 60l18-8v22l-18-8z" fill="#fff"/>
    <path d="M78 46l4-4M82 52h5M80 49l5-2" stroke="#fff" stroke-width="2"/>
  </svg>
  <div class="service-label">PROMOTIONAL</div>
</div>

<footer class="site-footer">
  <h2 class="footer-heading" style="left:81px">OUR LINK</h2>
  <ul class="link-list">
    <li>About US</li><li>Signage</li><li>Printing</li><li>Design</li><li>Promotional ...</li>
  </ul>

  <h2 class="footer-heading" style="left:222px">LATEST TWEET`S</h2>
  <svg class="tweet" width="15" height="15" viewBox="0 0 15 15"><rect width="15" height="15" rx="3" fill="#5a5a5a"/></svg>
  <p class="tweet-text">Phasellus porta. Fusce susct varius mi. Cum sociis natoque penabus et magnis dis parturient montes, nascetur ridiculus mus.</p>
  <div class="btn-more">See more</div>

  <h2 class="footer-heading" style="left:478px">CONTACT</h2>
  <ul class="contact-list">
    <li>(555) 214 7730 &nbsp; ( Office )</li>
    <li>(555) 398 1142 &nbsp; ( Cell )</li>
    <li class="email">www.info@velmarks.com</li>
    <li class="address"># 123 &nbsp;Our Street, Our City<br>our country ,CA 987.</li>
  </ul>

  <h2 class="footer-heading" style="left:680px">NEWSLETTER SIGNUP</h2>
  <p class="news-text">There are many variations of passages of Lorem available, but the majority</p>
  <div class="news-form">
    <span class="news-input">Email Addres</span>
    <div class="news-send">
      <svg width="37" height="35" viewBox="0 0 37 35"><path d="M11 18l15-7-5 15-3-6z" fill="none" stroke="#fff" stroke-width="1.6" stroke-linejoin="round"/></svg>
    </div>
  </div>
  <svg class="social" width="200" height="28" viewBox="0 0 200 28">
    <g stroke="#fff" stroke-width="2">
      <circle cx="13" cy="13" r="12" fill="#3b5998"/>
      <circle cx="46" cy="13" r="12" fill="#1da1f2"/>
      <circle cx="79" cy="13" r="12" fill="#d34836"/>
      <circle cx="112" cy="13" r="12" fill="#0e76a8"/>
      <circle cx="145" cy="13" r="12" fill="#c8232c"/>
      <circle cx="177" cy="13" r="12" fill="#7a8fc4"/>
    </g>
  </svg>
</footer>

<div class="bottom-bar">
  <span style="left:82px">Copyright © 2016 - Vel Marks.com</span>
  <span style="left:505px">Terms of Use</span>
  <span style="left:595px">Legal disclaimer</span>
  <span style="left:702px">Privacy Policy</span>
  <span style="left:795px">Support</span>
  <span style="left:859px">Sitemap</span>
</div>

</body>
</html>
```